Professional Services - letterhead / business cards

The company (velmora partners) will provide services to Investment Funds and large investors in Spain. I have recently chosen a logo that I am attaching.

I would like a simple stationary design that i could use as letter head, business cards and "with compliments" cards.

I am not quite sure which color I will mostly use for the logo, in the email signature I will probably lean towards the white background and grey letters. I am attaching my favourite options.

Target Market(s)

Large Multinationals, Investment funds and Law firms

Industry/Entity Type

Business

Requirements
Must have
• my details are:
Luis R. Abadal
Velmora Partners S.L.
Casa de Torrelumbre
Calle de Vientoalto 27
28014 Madrid
T: +34 (91) 387-2265
M: +34 (646) 819-054
e-mail: labadal@velmorapartners.com

```html
<!DOCTYPE html>
<html lang="en">
<head>
<meta charset="utf-8">
<title>Velmora Partners – Business Card</title>
<link rel="stylesheet" href="https://fonts.googleapis.com/css2?family=Mulish:wght@400;500&display=swap">
<style>
  :root {
    --navy: #2b2a6b;
    --paper: #ffffff;
    --ink: #2e2c6e;
    --backdrop: #e9e7e3;
    --shadow: rgba(0, 0, 0, 0.18);
  }
  * { box-sizing: border-box; margin: 0; padding: 0; }
  html, body {
    width: 1200px;
    height: 900px;
    overflow: hidden;
    background: var(--backdrop);
  }
  .canvas {
    position: relative;
    width: 1200px;
    height: 900px;
    font-family: "Mulish", sans-serif;
  }
  .card {
    position: absolute;
    left: 320px;
    width: 560px;
    height: 320px;
    box-shadow: 0 6px 18px var(--shadow);
  }
  .card--front {
    top: 100px;
    background: var(--navy);
  }
  .card--back {
    top: 480px;
    background: var(--paper);
    color: var(--ink);
  }
  .brand {
    position: absolute;
    right: 36px;
    bottom: 38px;
    display: flex;
    align-items: center;
    gap: 12px;
  }
  .brand__mark {
    width: 14px;
    height: 14px;
    background: var(--paper);
  }
  .brand__name {
    font-size: 26px;
    font-weight: 400;
    color: var(--paper);
    letter-spacing: 1px;
    white-space: nowrap;
  }
  .holder {
    position: absolute;
    left: 28px;
    top: 30px;
  }
  .holder__name {
    font-size: 19px;
    font-weight: 500;
    letter-spacing: 1.6px;
    text-transform: uppercase;
  }
  .holder__company {
    font-size: 13px;
    margin-top: 2px;
  }
  .details {
    position: absolute;
    left: 300px;
    top: 142px;
    bottom: 0;
    padding-left: 14px;
    border-left: 1px solid var(--ink);
    font-size: 13.5px;
    line-height: 1.35;
  }
  .contact-row {
    display: flex;
  }
  .contact-row__label {
    width: 20px;
  }
  .address {
    margin-top: 18px;
    font-style: normal;
  }
</style>
</head>
<body>
<main class="canvas">
  <section class="card card--front" aria-label="Business card front">
    <div class="brand">
      <span class="brand__mark" aria-hidden="true"></span>
      <p class="brand__name">Velmora Partners</p>
    </div>
  </section>

  <section class="card card--back" aria-label="Business card back">
    <div class="holder">
      <h1 class="holder__name">Luis R. Abadal</h1>
      <p class="holder__company">Velmora Partners S.L.</p>
    </div>
    <div class="details">
      <p class="contact-row"><span class="contact-row__label">T</span><span>+34 (91) 387-2265</span></p>
      <p class="contact-row"><span class="contact-row__label">M</span><span>+34 (646) 819-054</span></p>
      <p class="contact-row"><span class="contact-row__label">E</span><span>labadal@velmorapartners.com</span></p>
      <address class="address">
        Casa de Torrelumbre<br>
        Calle de Vientoalto 27,<br>
        28014 Madrid
      </address>
    </div>
  </section>
</main>
</body>
</html>
```